Harbor Crestline (Business Card Design)

Need business cards designed. Something modern, chic, and sleek. Mabye the back of the card should be the navy blue that is in the logo and then just the logo on the back.

Target Market(s)

Those in the hotel, office, and renovation industry

Contact Information for Business Card

1. Logo 2. Dorian Fenwick 3. CEO/Founder 4. Phone: (833) HarbCre / (833) 427-2731 5. Email: dorian@theharborcrestline.com 6. Website: www.theharborcrestline.com

Font styles to use
Other font styles liked:
• Look at the logo font and base the font for everything else off of that.

Colors
0054AA
0677BA
7BADD7
CADEEF
E8F1F8

Requirements
Must have
• Colors that are associated in the logo
Nice to have
• Sleek modern clean and chic design.

```html
<!DOCTYPE html>
<html lang="en">
<head>
<meta charset="utf-8">
<title>Harbor Crestline — Business Card</title>
<link href="https://fonts.googleapis.com/css2?family=Montserrat:wght@500;600;700&family=Poppins:wght@400&display=swap" rel="stylesheet">
<style>
  :root {
    --page: #ffffff;
    --navy: #0f1733;
    --navy-deep: #0b1026;
    --white: #ffffff;
    --gold: #d4a936;
    --shadow: rgba(0, 0, 0, 0.35);
  }
  * { box-sizing: border-box; margin: 0; padding: 0; }
  html, body {
    width: 690px;
    height: 1200px;
    overflow: hidden;
    background: var(--page);
  }
  .sheet {
    position: relative;
    width: 690px;
    height: 1200px;
  }
  .card {
    position: absolute;
    left: 65px;
    width: 560px;
    height: 320px;
    box-shadow: 10px 14px 18px var(--shadow);
    overflow: hidden;
  }
  .card--front {
    top: 230px;
    background: var(--navy);
  }
  .card--back {
    top: 640px;
    background: var(--navy-deep);
  }

  /* Front: centred brand */
  .brand {
    position: absolute;
    left: 0;
    right: 0;
    top: 72px;
    display: flex;
    flex-direction: column;
    align-items: center;
    gap: 30px;
  }
  .brand__mark {
    width: 84px;
    height: 84px;
    background: var(--gold);
  }
  .brand__name {
    font-family: "Montserrat", sans-serif;
    font-weight: 600;
    font-size: 34px;
    line-height: 1;
    letter-spacing: 3px;
    color: var(--white);
    text-transform: uppercase;
    white-space: nowrap;
  }

  /* Back: large brand block on the left */
  .feature {
    position: absolute;
    left: 34px;
    top: 0;
    bottom: 0;
    width: 220px;
    display: flex;
    flex-direction: column;
    justify-content: center;
    gap: 22px;
  }
  .feature__mark {
    width: 60px;
    height: 60px;
    background: var(--gold);
  }
  .feature__name {
    font-family: "Montserrat", sans-serif;
    font-weight: 700;
    font-size: 34px;
    line-height: 1.1;
    color: var(--white);
    text-transform: uppercase;
  }

  /* Back: contact details */
  .contact {
    position: absolute;
    right: 18px;
    top: 78px;
    text-align: right;
  }
  .contact__name {
    font-family: "Montserrat", sans-serif;
    font-weight: 700;
    font-size: 28px;
    line-height: 1.1;
    color: var(--white);
    text-transform: uppercase;
    white-space: nowrap;
  }
  .contact__surname { color: var(--gold); }
  .contact__role {
    font-family: "Montserrat", sans-serif;
    font-weight: 600;
    font-size: 15px;
    color: var(--gold);
    margin-top: 2px;
  }
  .contact__list {
    list-style: none;
    margin-top: 36px;
    font-family: "Poppins", sans-serif;
    font-weight: 400;
    font-size: 14px;
    line-height: 22px;
    color: var(--white);
  }
</style>
</head>
<body>
  <main class="sheet">
    <section class="card card--front" aria-label="Card front">
      <div class="brand">
        <span class="brand__mark" aria-hidden="true"></span>
        <h1 class="brand__name">Harbor Crestline</h1>
      </div>
    </section>

    <section class="card card--back" aria-label="Card back">
      <div class="feature">
        <span class="feature__mark" aria-hidden="true"></span>
        <p class="feature__name">Harbor<br>Crestline</p>
      </div>
      <div class="contact">
        <h2 class="contact__name">Dorian <span class="contact__surname">Fenwick</span></h2>
        <p class="contact__role">CEO/Founder</p>
        <ul class="contact__list">
          <li>(833) 427-2731</li>
          <li>(833) HarbCre</li>
          <li>dorian@theharborcrestline.com</li>
          <li>www.theharborcrestline.com</li>
        </ul>
      </div>
    </section>
  </main>
</body>
</html>
```